Business Cards for new orthopaedic surgery practice

My husband and I are starting our own orthopaedic surgery practice. We are looking for a business card that is uniform, but one will have my name/title and the other will have his. You can just create one design with my name on it for now. But when I choose your design as the winning design I will ask that you add another copy with his name/title.

We are looking for classy, simple, elite all in one. We like dark blues/a little gold/yellow. Something that goes with our logo. We want our logo incorporated. Here is all the info you need:
Business name: RV Bone & Vitality Center
Location: 38517 North Willowmere Ave
Palm Haven, FL 33482
Phone: 954-218-4063
Fax: 954-582-7341
Email: info@myrvbonecare.example

Names: Lydia Vance, M.D.
Board Certified Hand and Upper Extremity Surgeon

Ebo Dansu, M.D.
Board Certified Hip & Knee Replacement/General Orthopaedic Surgeon

Can decide what you want to put on the back. Maybe a slogan:
Grounded in Care. Centered on You

I am just going to upload our logo. The only thing is if we select you as the winning design, the location, and phone numbers may change. We will need your help to update that once fully solidified.

Industry/Entity Type

Medical

Contact Information for Business Card

Colors
0054AA
0677BA
7BADD7
CADEEF
E8F1F8
0094D4
00A9DD
6FCCEA
C7EBF8
E9F6FB

Requirements
Must have
• class, appeal,
Should not have
• We want to air on the side of masculine if we are looking at masculine vs. feminine feel. But we still want it classy, sophisticated, and something we will love

```html
<!DOCTYPE html>
<html lang="en">
<head>
<meta charset="utf-8">
<title>RV Bone &amp; Vitality Center – Business Card</title>
<link href="https://fonts.googleapis.com/css2?family=Montserrat:wght@400;500;600;700&family=Lato:wght@700&display=swap" rel="stylesheet">
<style>
  :root {
    --backdrop: #383838;
    --navy: #223a7e;
    --cyan: #19b2de;
    --paper: #f2f0f5;
    --white: #ffffff;
    --ink: #1f1f24;
  }
  * { margin: 0; padding: 0; box-sizing: border-box; }
  html, body { width: 1200px; height: 554px; overflow: hidden; background: var(--backdrop); }
  .stage { position: relative; width: 1200px; height: 554px; }
  .card {
    position: absolute; top: 128px; width: 523px; height: 298px;
    border-radius: 16px; overflow: hidden;
  }
  .card-front { left: 68px; background: var(--paper); }
  .card-back { left: 607px; background: var(--navy); }

  .wave { position: absolute; left: 0; top: 0; width: 523px; height: 298px; }

  .holder { position: absolute; left: 20px; top: 50px; }
  .holder-name {
    font-family: "Montserrat", sans-serif; font-weight: 700; font-size: 20px;
    color: var(--navy); letter-spacing: 0.2px; line-height: 1.2;
  }
  .holder-title {
    font-family: "Montserrat", sans-serif; font-weight: 500; font-size: 12.5px;
    color: var(--ink); margin-top: 5px;
  }

  .brand-front {
    position: absolute; right: 20px; top: 44px; display: flex; align-items: center; gap: 10px;
  }
  .brand-dot { width: 12px; height: 12px; border-radius: 50%; background: var(--navy); }
  .brand-name {
    font-family: "Montserrat", sans-serif; font-weight: 700; font-size: 14px; line-height: 1.3;
    color: var(--navy); text-transform: uppercase;
  }

  .contacts { position: absolute; left: 20px; top: 198px; list-style: none; }
  .contacts li {
    display: flex; align-items: center; gap: 6px; height: 20.5px;
    font-family: "Montserrat", sans-serif; font-weight: 500; font-size: 13px; color: var(--white);
  }
  .contacts svg { width: 12px; height: 12px; flex: none; }

  .address {
    position: absolute; right: 20px; top: 240px; text-align: right; font-style: normal;
    font-family: "Montserrat", sans-serif; font-weight: 500; font-size: 13px; line-height: 19px;
    color: var(--white);
  }

  .brand-back {
    position: absolute; left: 160px; right: 20px; top: 150px; text-align: center; color: var(--white);
  }
  .brand-back-name {
    font-family: "Montserrat", sans-serif; font-weight: 600; font-size: 21px; letter-spacing: 0.5px;
    text-transform: uppercase;
  }
  .brand-back-sub {
    display: flex; align-items: center; justify-content: center; gap: 8px; margin-top: 4px;
    font-family: "Montserrat", sans-serif; font-weight: 600; font-size: 16px; letter-spacing: 2px;
  }
  .brand-back-sub .rule { width: 58px; height: 1.5px; background: var(--white); }
  .slogan {
    margin-top: 14px; font-family: "Lato", sans-serif; font-weight: 700; font-size: 11.5px;
  }
</style>
</head>
<body>
<main class="stage">

  <section class="card card-front" aria-label="Business card front">
    <svg class="wave" viewBox="0 0 523 298" aria-hidden="true">
      <path fill="var(--cyan)" d="M7 172 C40 150 80 136 120 136 C200 136 300 188 380 190 C440 192 480 176 500 164 C480 184 440 196 380 196 C300 194 200 146 120 144 C80 144 40 158 7 174 Z"/>
      <path fill="var(--navy)" d="M0 182 C40 162 80 150 120 152 C200 156 300 198 375 199 C440 200 490 180 523 154 L523 298 L0 298 Z"/>
    </svg>

    <div class="holder">
      <h1 class="holder-name">LYDIA VANCE, M.D.</h1>
      <p class="holder-title">Hand and Upper Extremity Surgery</p>
    </div>

    <div class="brand-front">
      <span class="brand-dot"></span>
      <p class="brand-name">RV Bone &amp;<br>Vitality<br>Center</p>
    </div>

    <ul class="contacts">
      <li>
        <svg viewBox="0 0 24 24"><path fill="var(--cyan)" d="M6.6 10.8a15 15 0 0 0 6.6 6.6l2.2-2.2a1 1 0 0 1 1-.25 11.4 11.4 0 0 0 3.6.57 1 1 0 0 1 1 1V20a1 1 0 0 1-1 1A17 17 0 0 1 3 4a1 1 0 0 1 1-1h3.5a1 1 0 0 1 1 1c0 1.25.2 2.45.57 3.57a1 1 0 0 1-.25 1z"/></svg>
        954-218-4063
      </li>
      <li>
        <svg viewBox="0 0 24 24"><path fill="var(--cyan)" d="M6 2h12v5H6zM3 8h18a2 2 0 0 1 2 2v7h-4v5H5v-5H1v-7a2 2 0 0 1 2-2zm4 7v5h10v-5z"/></svg>
        954-582-7341
      </li>
      <li>
        <svg viewBox="0 0 24 24"><path fill="var(--cyan)" d="M2 5h20v14H2zm2 2v.4l8 5 8-5V7l-8 5z"/></svg>
        info@myrvbonecare.example
      </li>
      <li>
        <svg viewBox="0 0 24 24"><circle cx="12" cy="12" r="10" fill="none" stroke="var(--cyan)" stroke-width="2"/><path fill="none" stroke="var(--cyan)" stroke-width="1.6" d="M2 12h20M12 2c3 3 3 17 0 20M12 2c-3 3-3 17 0 20"/></svg>
        www.myrvbonecare.example
      </li>
    </ul>

    <address class="address">
      38517 North Willowmere Ave<br>
      Palm Haven, FL 33482
    </address>
  </section>

  <section class="card card-back" aria-label="Business card back">
    <div class="brand-back">
      <p class="brand-back-name">RV Bone &amp; Vitality</p>
      <p class="brand-back-sub"><span class="rule"></span>CENTER<span class="rule"></span></p>
      <p class="slogan">Grounded in Care. Centered on You</p>
    </div>
  </section>

</main>
</body>
</html>
```